Animal Horse & Bedding Company Needs a Website Coded & Designed

We need a website for a new animal bedding and feed company that is visually grabbing and vibrant. We would like to see a website that displays trust, quality and confidence. Needs to be responsive and mobile friendly for all browsers and coded for both Android & IOS. SEO is also important.

Joomla or Wordpress – must be both desktop and mobile friendly with fast page load speed. Need the ability to edit ourselves in Wordpress or Joomla.

Full details attached below with some layout and content ideas.

Coding

Coded - Design and coding required

Number of Pages Required

5+ page

Font styles to use
Sans Serif

Requirements
Must have
• Needs to be responsive and mobile friendly for all browsers and coded for both Android & IOS. SEO is also important.

Wordpress – must be both desktop and mobile friendly with fast page load speed. Need the ability to edit ourselves in Wordpress.

Logo Colours:
Dark Brown
CMYK: 50 / 70 / 80 / 70
Pantone: 4625C

Orange
CMYK: 0 / 50 / 100 / 0
Pantone: 144C
Nice to have
• Use picture of building attached and super impose logo on building.

```html
<!DOCTYPE html>
<html lang="en">
<head>
<meta charset="utf-8">
<title>Golden Furrow – Bedding &amp; Feed</title>
<link rel="stylesheet" href="https://fonts.googleapis.com/css2?family=Oswald:wght@400;500;600&family=Source+Sans+3:wght@400;600;700&display=swap">
<style>
:root{
  --brown:#3b2314;
  --brown-deep:#2e1a0e;
  --orange:#f7941d;
  --orange-soft:#f9a233;
  --cream:#fdf6ee;
  --text:#4a3a30;
  --white:#ffffff;
}
*{box-sizing:border-box;margin:0;padding:0}
html,body{width:1200px;height:2827px;overflow:hidden}
body{position:relative;font-family:"Source Sans 3",Arial,sans-serif;color:var(--text);background:var(--white)}
.abs{position:absolute}
.heading{font-family:"Oswald","Arial Narrow",sans-serif;font-weight:500;letter-spacing:.5px}

/* top bar */
.topbar{left:0;top:0;width:1200px;height:24px;background:var(--brown);color:var(--white);font-size:11px;font-weight:700}
.topbar .call{left:122px;top:5px}
.topbar .call span{color:var(--orange)}
.topbar .follow{right:104px;top:5px;display:flex;align-items:center;gap:3px}
.dot{width:12px;height:12px;border-radius:50%;background:var(--orange);display:inline-block}

/* hero */
.hero{left:0;top:24px;width:1200px;height:656px;background:linear-gradient(180deg,#efe4ea 0%,#f3dcc4 30%,#e6cfa6 45%,#9fa56a 55%,#7f8d4c 75%,#6a7a3c 100%)}
.nav a{position:absolute;top:60px;font-family:"Oswald","Arial Narrow",sans-serif;font-size:19px;color:var(--brown);text-decoration:none;letter-spacing:.3px}
.brand{display:flex;align-items:center;gap:10px}
.brand .mark{width:34px;height:34px;border-radius:50%;background:var(--orange)}
.brand .name{font-family:"Oswald","Arial Narrow",sans-serif;font-weight:400;font-size:34px;letter-spacing:3px;color:var(--brown)}
.btn{display:inline-flex;align-items:center;justify-content:center;border-radius:16px;font-family:"Oswald","Arial Narrow",sans-serif;font-size:14px;text-decoration:none}
.btn-dark{background:var(--brown);color:var(--orange)}
.btn-ghost{border:1.5px solid var(--orange);color:var(--brown);background:rgba(255,255,255,.25)}
.hero-title{left:200px;top:142px;width:568px;text-align:center;font-size:40px;line-height:40px;color:var(--brown);font-weight:600}

/* welcome */
.welcome-label{font-size:15px;color:var(--brown)}
.welcome-copy{left:117px;top:853px;width:420px;font-size:12.6px;line-height:16px;text-align:justify}
.welcome-copy p{margin-bottom:14px}
.farm{left:571px;top:768px;width:473px;height:265px;background:linear-gradient(180deg,#c9d3dc 0%,#aab7c0 30%,#6c7a57 45%,#7a6b55 65%,#5d6a44 100%)}
.feature{display:flex;gap:10px;align-items:flex-start}
.feature .ico{width:36px;height:36px;border-radius:50%;background:var(--orange);border:2px solid var(--brown);flex:none}
.feature h4{font-family:"Source Sans 3",Arial,sans-serif;font-size:13.5px;font-weight:700;color:var(--brown);text-transform:uppercase}
.feature p{font-size:10px;line-height:12px;color:var(--brown)}
.divider{width:2px;height:56px;background:var(--brown);opacity:.6}

/* services */
.services{left:0;top:1225px;width:1200px;height:1130px;background:linear-gradient(180deg,#3d4148 0%,#4a4038 20%,#6b5a3c 40%,#4a3a26 100%)}
.services-title{left:0;top:1286px;width:1200px;text-align:center;font-size:46px;color:var(--orange);font-weight:600;letter-spacing:1.5px}
.photo{height:379px;top:1417px}
.card{top:1795px;width:545px;height:484px;background:var(--brown);color:var(--white)}
.card h3{position:absolute;left:72px;top:38px;font-size:33px;color:var(--orange);font-weight:600;letter-spacing:1.5px}
.card .rule{position:absolute;left:72px;top:90px;width:50px;height:2px;background:var(--orange)}
.card .lead{position:absolute;left:50px;top:120px;width:420px;font-size:15px;line-height:16px;text-align:justify}
.card ul{position:absolute;left:50px;top:216px;list-style:none}
.card li{display:flex;align-items:center;gap:8px;font-size:15px;height:24px}
.card li svg{flex:none}
.read{position:absolute;left:52px;width:110px;height:32px;background:var(--orange);color:var(--brown);border-radius:16px;font-size:10px;font-weight:700;letter-spacing:1px;display:flex;align-items:center;justify-content:center}

/* newsletter */
.news{left:0;top:2355px;width:1200px;height:198px;background:linear-gradient(180deg,#b9cde0 0%,#d7e2ea 40%,#c6c59a 70%,#7b8a46 100%)}
.news-title{left:344px;top:2400px;font-size:34px;color:var(--brown);font-weight:600;letter-spacing:1.5px}
.news-form{left:315px;top:2459px;width:836px;height:50px;display:flex;border:1px solid #9c8a7a}
.news-form .field{flex:1;background:var(--white);font-size:14px;color:#5a4a40;padding:15px 40px}
.news-form .go{width:128px;background:var(--brown);color:var(--white);font-size:15px;font-weight:700;display:flex;align-items:center;justify-content:center}

/* footer */
.footer{left:0;top:2553px;width:1200px;height:233px;background:var(--brown);color:var(--white)}
.footer h5{position:absolute;font-family:"Oswald","Arial Narrow",sans-serif;font-weight:400;font-size:15px;color:var(--orange);text-decoration:underline;text-underline-offset:3px}
.footer ul{position:absolute;list-style:none;font-size:11.5px}
.footer li{display:flex;align-items:center;gap:8px;height:18.5px}
.tri{width:0;height:0;border-left:6px solid var(--orange);border-top:4px solid transparent;border-bottom:4px solid transparent}
.mini-form{left:910px;top:2637px;width:163px;height:26px;display:flex}
.mini-form .field{flex:1;background:var(--white);font-size:9px;color:#7a6a60;padding:8px 12px}
.mini-form .go{width:28px;background:var(--orange);display:flex;align-items:center;justify-content:center}
.bottombar{left:0;top:2786px;width:1200px;height:41px;background:var(--orange);color:var(--brown);font-size:13px}
</style>
</head>
<body>

<div class="abs topbar">
  <div class="abs call">Call Us : <span>+1 555 010 2468</span></div>
  <div class="abs follow">Follow Us: <i class="dot"></i><i class="dot"></i><i class="dot"></i><i class="dot"></i><i class="dot"></i></div>
</div>

<section class="abs hero" role="img" aria-label="Sunrise pasture with a chestnut horse standing in the foreground and another grazing behind"></section>

<nav class="nav">
  <a href="#" style="left:135px">HOME</a>
  <a href="#" style="left:232px">ABOUT</a>
  <a href="#" style="left:335px">FEED</a>
  <a href="#" style="left:800px;top:53px">BEDDING</a>
  <a href="#" style="left:902px;top:53px">CONTACT US</a>
</nav>
<div class="abs brand" style="left:455px;top:46px"><span class="mark"></span><span class="name">GOLDEN FURROW</span></div>
<a class="abs btn btn-dark" href="#" style="left:1002px;top:49px;width:128px;height:31px;font-size:15px">REQUEST QOUTE</a>

<h1 class="abs heading hero-title">THE BEST BEDDING &amp; FEED FOR YOUR HORSE LIVESTOCK OR HOUSEHOLD PET</h1>
<a class="abs btn btn-dark" href="#" style="left:359px;top:279px;width:111px;height:33px">CONTACT US</a>
<a class="abs btn btn-ghost" href="#" style="left:497px;top:279px;width:111px;height:33px">REQUEST QUOTE</a>

<!-- welcome -->
<div class="abs" style="left:117px;top:758px">
  <div class="heading welcome-label">WELCOME TO</div>
  <div class="brand" style="margin-top:2px"><span class="mark" style="width:40px;height:40px"></span><span class="name" style="font-size:36px">GOLDEN FURROW</span></div>
</div>
<div class="abs welcome-copy">
  <p>Looking for the best bedding and feed for your horse, livestock or household pet look no further. We use premium locally sourced straw and hay in all of our products and are committed in providing quality products and service.</p>
  <p>Your animal deserves the very best in health and comfort to keep them healthy, strong and happy. Our products are designed for horses, livestock (goats, cattle and sheep), small caged animals (rabbits, guinea pigs and more).</p>
  <p>Golden Furrow offers supply and delivery of fresh bedding as well as removal of waste bedding. Let us deliver you a container of fresh straw and haul your waste bedding away. A full service solution that is sustainable and responsible.</p>
</div>
<div class="abs farm" role="img" aria-label="Aerial view of a farm with red barns and paddocks"></div>

<div class="abs feature" style="left:117px;top:1064px;width:240px">
  <span class="ico"></span>
  <div><h4>Quality Guaranteed</h4><p>Grown for quality - 100% natural with no<br>chemicals or additives</p></div>
</div>
<div class="abs divider" style="left:383px;top:1050px"></div>
<div class="abs feature" style="left:436px;top:1064px;width:260px">
  <span class="ico"></span>
  <div><h4>Full Service Solution</h4><p>Dedicated in providing a full service solution<br>of bedding supply &amp; waste removal</p></div>
</div>
<div class="abs divider" style="left:715px;top:1050px"></div>
<div class="abs feature" style="left:769px;top:1063px;width:270px">
  <span class="ico"></span>
  <div><h4>Convenient &amp; Cost Effective</h4><p>Compressed bags, pellets or bulk products saving<br>in shipping costs</p></div>
</div>

<!-- services -->
<section class="abs services" role="img" aria-label="Round hay bales in a field under a cloudy sky"></section>
<h2 class="abs heading services-title">OUR SERVICES</h2>
<div class="abs photo" style="left:47px;width:545px;background:linear-gradient(135deg,#b07a3a 0%,#d9a440 40%,#e8b84a 70%,#c58f2e 100%)" role="img" aria-label="Mare and foal resting on straw bedding"></div>
<div class="abs photo" style="left:618px;width:545px;background:linear-gradient(90deg,#c78634 0%,#b99a78 40%,#d9d2c8 60%,#2a1c14 100%)" role="img" aria-label="Close view of a horse eating hay"></div>

<article class="abs card" style="left:47px">
  <h3 class="heading">BEDDING</h3><span class="rule"></span>
  <p class="lead">Hay cubes and pellets are made from premium hay offering a variety of animals a feed that is non-GMO and packed with natural nutrients. These pellets and cubes are less bulky to handle, store and ship.As well, they reduce the amount of wasted feed.</p>
  <ul>
    <li><svg width="12" height="12" viewBox="0 0 12 12"><circle cx="6" cy="6" r="6" fill="#f7941d"/><path d="M3.2 6.2l1.9 1.8 3.7-3.8" stroke="#3b2314" stroke-width="1.4" fill="none"/></svg>100% Natural Chopped Straw</li>
    <li><svg width="12" height="12" viewBox="0 0 12 12"><circle cx="6" cy="6" r="6" fill="#f7941d"/><path d="M3.2 6.2l1.9 1.8 3.7-3.8" stroke="#3b2314" stroke-width="1.4" fill="none"/></svg>Low Dust</li>
    <li><svg width="12" height="12" viewBox="0 0 12 12"><circle cx="6" cy="6" r="6" fill="#f7941d"/><path d="M3.2 6.2l1.9 1.8 3.7-3.8" stroke="#3b2314" stroke-width="1.4" fill="none"/></svg>Chemical &amp; Additive Free</li>
    <li><svg width="12" height="12" viewBox="0 0 12 12"><circle cx="6" cy="6" r="6" fill="#f7941d"/><path d="M3.2 6.2l1.9 1.8 3.7-3.8" stroke="#3b2314" stroke-width="1.4" fill="none"/></svg>Clean &amp; Highly Absorbent</li>
    <li><svg width="12" height="12" viewBox="0 0 12 12"><circle cx="6" cy="6" r="6" fill="#f7941d"/><path d="M3.2 6.2l1.9 1.8 3.7-3.8" stroke="#3b2314" stroke-width="1.4" fill="none"/></svg>Cheaper than Wood Shavings</li>
    <li><svg width="12" height="12" viewBox="0 0 12 12"><circle cx="6" cy="6" r="6" fill="#f7941d"/><path d="M3.2 6.2l1.9 1.8 3.7-3.8" stroke="#3b2314" stroke-width="1.4" fill="none"/></svg>Economic – less used &amp; less wasted</li>
    <li><svg width="12" height="12" viewBox="0 0 12 12"><circle cx="6" cy="6" r="6" fill="#f7941d"/><path d="M3.2 6.2l1.9 1.8 3.7-3.8" stroke="#3b2314" stroke-width="1.4" fill="none"/></svg>Environmentally Friendly – Recyclable &amp; Compostable</li>
  </ul>
  <a class="read" href="#" style="top:400px">READ MORE</a>
</article>

<article class="abs card" style="left:623px">
  <h3 class="heading" style="left:85px">FEEDING</h3><span class="rule" style="left:85px"></span>
  <p class="lead" style="left:57px">Hay cubes and pellets are made from premium hay offering a variety of animals a feed that is non-GMO and packed with natural nutrients. These pellets and cubes are less bulky to handle, store and ship.As well, they reduce the amount of wasted feed.</p>
  <ul style="left:53px;top:214px">
    <li><svg width="12" height="12" viewBox="0 0 12 12"><circle cx="6" cy="6" r="6" fill="#f7941d"/><path d="M3.2 6.2l1.9 1.8 3.7-3.8" stroke="#3b2314" stroke-width="1.4" fill="none"/></svg>100% Natural</li>
    <li><svg width="12" height="12" viewBox="0 0 12 12"><circle cx="6" cy="6" r="6" fill="#f7941d"/><path d="M3.2 6.2l1.9 1.8 3.7-3.8" stroke="#3b2314" stroke-width="1.4" fill="none"/></svg>Chemical &amp; Additive Free</li>
    <li><svg width="12" height="12" viewBox="0 0 12 12"><circle cx="6" cy="6" r="6" fill="#f7941d"/><path d="M3.2 6.2l1.9 1.8 3.7-3.8" stroke="#3b2314" stroke-width="1.4" fill="none"/></svg>Available in Pellets or Cubes</li>
    <li><svg width="12" height="12" viewBox="0 0 12 12"><circle cx="6" cy="6" r="6" fill="#f7941d"/><path d="M3.2 6.2l1.9 1.8 3.7-3.8" stroke="#3b2314" stroke-width="1.4" fill="none"/></svg>High Protein Content</li>
    <li><svg width="12" height="12" viewBox="0 0 12 12"><circle cx="6" cy="6" r="6" fill="#f7941d"/><path d="M3.2 6.2l1.9 1.8 3.7-3.8" stroke="#3b2314" stroke-width="1.4" fill="none"/></svg>Eliminate Waste In Feeding</li>
    <li><svg width="12" height="12" viewBox="0 0 12 12"><circle cx="6" cy="6" r="6" fill="#f7941d"/><path d="M3.2 6.2l1.9 1.8 3.7-3.8" stroke="#3b2314" stroke-width="1.4" fill="none"/></svg>Clean - Eliminates Dust From Feeding Baled Hay</li>
    <li><svg width="12" height="12" viewBox="0 0 12 12"><circle cx="6" cy="6" r="6" fill="#f7941d"/><path d="M3.2 6.2l1.9 1.8 3.7-3.8" stroke="#3b2314" stroke-width="1.4" fill="none"/></svg>Cost Effective</li>
  </ul>
  <a class="read" href="#" style="left:57px;top:408px">READ MORE</a>
</article>

<!-- newsletter -->
<section class="abs news" role="img" aria-label="Mare and foal standing in a grassy meadow"></section>
<h2 class="abs heading news-title">SUBSCRIBE TO NEWSLETTER</h2>
<div class="abs news-form"><div class="field">Enter Your Email</div><div class="go">SUBSCRIBE</div></div>

<!-- footer -->
<footer class="abs footer">
  <div class="abs" style="left:130px;top:52px;width:240px;text-align:center">
    <span class="mark" style="display:block;margin:0 auto 12px;width:46px;height:46px;border-radius:50%;background:var(--orange)"></span>
    <span style="font-family:'Oswald','Arial Narrow',sans-serif;font-size:34px;letter-spacing:3px;color:var(--white)">GOLDEN FURROW</span>
  </div>
  <h5 style="left:451px;top:52px">QUICK LINKS</h5>
  <ul style="left:453px;top:82px">
    <li><i class="tri"></i>Home</li><li><i class="tri"></i>About</li><li><i class="tri"></i>Feed</li><li><i class="tri"></i>Bedding</li><li><i class="tri"></i>Contact Us</li>
  </ul>
  <h5 style="left:653px;top:54px">CONTACT US</h5>
  <ul style="left:653px;top:84px;line-height:18.5px">
    <li style="align-items:flex-start;height:37px"><svg width="10" height="12" viewBox="0 0 10 12" style="margin-top:3px"><path d="M5 0a4 4 0 0 0-4 4c0 3 4 8 4 8s4-5 4-8a4 4 0 0 0-4-4z" fill="#f7941d"/><circle cx="5" cy="4" r="1.5" fill="#3b2314"/></svg><span>412 Meadowgate Road<br>Brookvale, Alaska 99501</span></li>
    <li><svg width="10" height="10" viewBox="0 0 10 10"><path d="M2 0l2 2.5-1 1.2a6 6 0 0 0 3.3 3.3l1.2-1L10 8l-1.5 2C4 10 0 6 0 1.5z" fill="#f7941d"/></svg>555-010-7731</li>
    <li><svg width="10" height="8" viewBox="0 0 10 8"><rect width="10" height="8" fill="#f7941d"/><path d="M0 0l5 4 5-4" stroke="#3b2314" fill="none"/></svg>hello@goldenfurrow.example</li>
    <li><svg width="10" height="10" viewBox="0 0 10 10"><circle cx="5" cy="5" r="4.3" stroke="#f7941d" fill="none"/><path d="M1 5h8M5 .7c-2 2.5-2 6 0 8.6M5 .7c2 2.5 2 6 0 8.6" stroke="#f7941d" stroke-width=".8" fill="none"/></svg>goldenfurrow.example</li>
  </ul>
  <h5 style="left:913px;top:52px">NEWSLETTER</h5>
  <h5 style="left:913px;top:122px">FOLLOW US</h5>
  <div class="abs" style="left:913px;top:152px;display:flex;gap:3px">
    <i class="dot" style="width:16px;height:16px;background:var(--white)"></i><i class="dot" style="width:16px;height:16px;background:var(--white)"></i><i class="dot" style="width:16px;height:16px;background:var(--white)"></i><i class="dot" style="width:16px;height:16px;background:var(--white)"></i><i class="dot" style="width:16px;height:16px;background:var(--white)"></i>
  </div>
</footer>
<div class="abs mini-form"><div class="field">Email Address</div><div class="go"><svg width="8" height="10" viewBox="0 0 8 10"><path d="M0 0l8 5-8 5z" fill="#3b2314"/></svg></div></div>

<div class="abs bottombar">
  <span class="abs" style="left:127px;top:12px">Copyright © 2021, Northfield Studio, All Right Reserved</span>
  <span class="abs" style="right:126px;top:12px">Delivery in Canada &amp; USA</span>
</div>

</body>
</html>
```